Business Cards Design for the electrical wholesaler: clean bold dynamic :)

We need a business card design that would follow our latest brand guidelines. As an electrical wholesaler we want to bring a fresh look and feel into the industry. The design should be clean bold and dynamic. It should come alive with the renewed energy of our green colour. Our grey colour should keep things balanced and complement the notion of maturity and responsibility. We employ Lato as a corporate font however are not bound by this font and we’re open to interpretation here.

Target Market(s)

Electrical contractors

Industry/Entity Type

Business

Contact Information for Business Card

Logo
Name & Surname: Halyna Dorosh
Job Title: Director of Marketing
Email: halya.dorosh@quillmail.example
Cell phone: XXX.XXX.XXXX
Address: 20517 - 87 Ave. Edmonton, AB, Canada. T6K 4N8
Business Phone: 780.555.0184
Website: www.brovix.example

Font styles to use
Other font styles liked:
• Lato

Requirements
Must have
• Logo & website
Nice to have
• Brand elements - some of them you may find in the attached Brand Guidelines (e.g. three lines on the background signifying "W")

```html
<!DOCTYPE html>
<html lang="en">
<head>
<meta charset="utf-8">
<title>Brovix Business Cards</title>
<link rel="stylesheet" href="https://fonts.googleapis.com/css2?family=Exo+2:wght@500&family=Roboto:wght@400;500&display=swap">
<style>
  :root {
    --backdrop: #b9b9b9;
    --green: #7ab51f;
    --green-deep: #5ea42a;
    --grey: #4a4d50;
    --grey-text: #55585b;
    --card-white: #f6f6f6;
    --card-silver: #e2e2e2;
  }
  html, body {
    margin: 0;
    padding: 0;
    overflow: hidden;
  }
  .canvas {
    position: relative;
    width: 1200px;
    height: 576px;
    background: var(--backdrop);
    overflow: hidden;
    font-family: "Roboto", sans-serif;
  }
  .card {
    position: absolute;
    top: 138px;
    border-radius: 13px;
    overflow: hidden;
    box-shadow: 0 3px 6px rgba(0,0,0,0.25);
  }
  .card-front {
    left: 82px;
    width: 484px;
    height: 294px;
    background: linear-gradient(160deg, var(--green) 0%, var(--green-deep) 100%);
  }
  .card-back {
    left: 602px;
    width: 480px;
    height: 292px;
    background: linear-gradient(135deg, var(--card-white) 0%, var(--card-silver) 100%);
  }
  .wordmark {
    position: absolute;
    display: flex;
    align-items: center;
    gap: 10px;
    font-family: "Roboto", sans-serif;
    font-weight: 500;
    color: var(--grey);
    line-height: 1;
  }
  .wordmark-square {
    background: var(--grey);
  }
  .card-front .wordmark {
    left: 50%;
    top: 50%;
    transform: translate(-50%, -50%);
    font-size: 44px;
  }
  .card-front .wordmark-square {
    width: 30px;
    height: 30px;
  }
  .side-band {
    position: absolute;
    left: 0;
    top: 0;
    width: 42px;
    height: 100%;
    background: var(--green);
  }
  .side-rule {
    position: absolute;
    left: 46px;
    top: 0;
    width: 3px;
    height: 100%;
    background: var(--grey);
  }
  .card-back .wordmark {
    left: 70px;
    top: 46px;
    font-size: 36px;
  }
  .card-back .wordmark-square {
    width: 24px;
    height: 24px;
  }
  .person-name {
    position: absolute;
    left: 72px;
    top: 136px;
    margin: 0;
    font-family: "Exo 2", sans-serif;
    font-weight: 500;
    font-size: 21px;
    color: var(--green);
  }
  .person-title {
    position: absolute;
    left: 72px;
    top: 163px;
    margin: 0;
    font-size: 12px;
    color: var(--grey-text);
  }
  .address {
    position: absolute;
    left: 72px;
    top: 196px;
    margin: 0;
    font-style: normal;
    font-size: 12.5px;
    line-height: 17px;
    color: var(--grey-text);
  }
  .contact-list {
    position: absolute;
    left: 72px;
    top: 237px;
    margin: 0;
    padding: 0;
    list-style: none;
    font-size: 12.5px;
    color: var(--grey-text);
  }
  .contact-row {
    display: flex;
    align-items: center;
    gap: 8px;
    height: 17px;
    white-space: nowrap;
  }
  .contact-item {
    display: flex;
    align-items: center;
    gap: 6px;
  }
  .contact-icon {
    width: 13px;
    height: 13px;
    flex: none;
  }
</style>
</head>
<body>
<main class="canvas">

  <section class="card card-front" aria-label="Card front">
    <div class="wordmark">
      <span class="wordmark-square"></span>
      <span class="wordmark-name">Brovix</span>
    </div>
  </section>

  <section class="card card-back" aria-label="Card back">
    <div class="side-band"></div>
    <div class="side-rule"></div>

    <div class="wordmark">
      <span class="wordmark-square"></span>
      <span class="wordmark-name">Brovix</span>
    </div>

    <h1 class="person-name">Halyna Dorosh</h1>
    <p class="person-title">Director of Marketing</p>

    <address class="address">20517 - 87 Ave. Edmonton,<br>AB, Canada T6K 4N8</address>

    <ul class="contact-list">
      <li class="contact-row">
        <span class="contact-item">
          <svg class="contact-icon" viewBox="0 0 14 14" aria-hidden="true">
            <circle cx="7" cy="7" r="6.3" fill="none" stroke="#7ab51f" stroke-width="1.2"/>
            <path d="M4.3 4.2 h1.6 l0.6 1.5 -0.9 0.8 a4 4 0 0 0 1.9 1.9 l0.8 -0.9 1.5 0.6 v1.6 a5.5 5.5 0 0 1 -5.5 -5.5z" fill="#7ab51f"/>
          </svg>
          <span>+1 780-555-0184</span>
        </span>
        <span class="contact-item">
          <svg class="contact-icon" viewBox="0 0 14 14" aria-hidden="true">
            <circle cx="7" cy="7" r="6.3" fill="none" stroke="#7ab51f" stroke-width="1.2"/>
            <rect x="5" y="3.4" width="4" height="7.2" rx="0.8" fill="#7ab51f"/>
          </svg>
          <span>+1 780-555-0147</span>
        </span>
      </li>
      <li class="contact-row">
        <span class="contact-item">
          <svg class="contact-icon" viewBox="0 0 14 14" aria-hidden="true">
            <circle cx="7" cy="7" r="6.3" fill="none" stroke="#7ab51f" stroke-width="1.2"/>
            <rect x="3.8" y="4.8" width="6.4" height="4.4" fill="#7ab51f"/>
            <path d="M3.8 4.8 L7 7.3 L10.2 4.8" fill="none" stroke="#f6f6f6" stroke-width="0.8"/>
          </svg>
          <span>halya.dorosh@quillmail.example</span>
        </span>
        <span class="contact-item">
          <svg class="contact-icon" viewBox="0 0 14 14" aria-hidden="true">
            <circle cx="7" cy="7" r="6.3" fill="none" stroke="#7ab51f" stroke-width="1.2"/>
            <circle cx="7" cy="7" r="3.4" fill="#7ab51f"/>
          </svg>
          <span>brovix.example</span>
        </span>
      </li>
    </ul>
  </section>

</main>
</body>
</html>
```